Computer Training in the Education sector - Letterhead

We need a new letter head to be designed for the company. We provide computer training fro the Education Sector, both primary and private tertiary providers. The colours will need to tie in with the website www.crossingthestream.co.nz.
The company name is Crossing the Stream with the tag line of Computer Training for Educators.
The footer will need to have the following detail...
0508 PCS MENTOR
021 839 415
www.crossingthestream.co.nz / training@crossingthestream.co.nz
Updates

Thanks for the designs so far.

Some have watermarks in the background. Please don't worry about using watermarks as I will not be using a watermark in in a final design.
Regards,
Roger

Thank you for all the designs and the effort. There was some great concepts that came through.

Cheers
Roger

Industry/Entity Type

Computer

```html
<!DOCTYPE html>
<html lang="en">
<head>
<meta charset="utf-8">
<title>Crossing the Stream – Letterhead</title>
<link rel="stylesheet" href="https://fonts.googleapis.com/css2?family=Tinos:wght@400;700&display=swap">
<style>
  :root {
    --paper-top: #a3ebf8;
    --paper-mid: #cff5fb;
    --paper-bottom: #f7fdfe;
    --brand-blue: #2f84e0;
    --accent-orange: #ec8a35;
    --footer-deep: #2a7bd6;
    --footer-light: #3f90e6;
    --footer-text: #ffffff;
    --link-blue: #3a88d8;
  }
  html, body {
    margin: 0;
    padding: 0;
    width: 848px;
    height: 1200px;
    overflow: hidden;
  }
  .letterhead {
    position: relative;
    width: 848px;
    height: 1200px;
    overflow: hidden;
    background: linear-gradient(180deg, var(--paper-top) 0%, var(--paper-mid) 45%, var(--paper-bottom) 85%);
    font-family: "Tinos", "Times New Roman", serif;
  }
  .brand {
    position: absolute;
    top: 52px;
    right: 52px;
    display: flex;
    align-items: center;
    gap: 10px;
  }
  .brand-dot {
    width: 16px;
    height: 16px;
    border-radius: 50%;
    background: var(--accent-orange);
  }
  .brand-name {
    margin: 0;
    font-size: 30px;
    font-weight: 700;
    line-height: 1.05;
    color: var(--brand-blue);
  }
  .web-address {
    position: absolute;
    top: 202px;
    right: 48px;
    margin: 0;
    font-size: 12px;
    font-weight: 700;
    letter-spacing: 0.8px;
    color: var(--link-blue);
  }
  .footer-band {
    position: absolute;
    left: 0;
    bottom: 0;
    width: 848px;
    height: 128px;
    background: linear-gradient(180deg, var(--footer-light) 0%, var(--footer-deep) 100%);
  }
  .contact {
    position: absolute;
    left: 596px;
    top: 1100px;
    margin: 0;
    padding: 0;
    list-style: none;
    font-size: 12px;
    font-weight: 700;
    letter-spacing: 0.6px;
    line-height: 24px;
    color: var(--footer-text);
  }
</style>
</head>
<body>
  <main class="letterhead">
    <header class="brand">
      <span class="brand-dot"></span>
      <h1 class="brand-name">Crossing<br>the Stream</h1>
    </header>
    <p class="web-address">www.crossingthestream.co.nz</p>

    <div class="footer-band" role="img" aria-label="Footer decoration of flowing colour bands in orange, green and blue"></div>

    <ul class="contact">
      <li>training@crossingthestream.co.nz</li>
      <li>0508 PCS MENTOR</li>
      <li>021 839 415</li>
    </ul>
  </main>
</body>
</html>
```